Corvane Capital Business Cards

These are professional business cards that are for my family office.
Put fake emails and phone numbers as of now until I finalize those components. This family office controls my families investments, assets, and future. The cards should be professional.
..
.
.
.
I just uploaded another variation of a logo I would like to see as a business card to I am inbeteen which logo to use

Target Market(s)

business

Industry/Entity Type

business

Contact Information for Business Card

Professional, wealth related, finance related.

Requirements
Must have
• Logo

```html
<!DOCTYPE html>
<html lang="en">
<head>
<meta charset="utf-8">
<title>Corvane Capital Business Cards</title>
<link rel="stylesheet" href="https://fonts.googleapis.com/css2?family=EB+Garamond:wght@400;500&display=swap">
<style>
  :root {
    --backdrop: #d8d9db;
    --card: #ffffff;
    --ink: #3b4049;
    --ink-soft: #5a5f67;
    --accent-bar: #2f3238;
    --ring: #4a4f58;
  }
  * { margin: 0; padding: 0; box-sizing: border-box; }
  html, body {
    width: 1200px;
    height: 900px;
    overflow: hidden;
    background: var(--backdrop);
    font-family: "EB Garamond", Georgia, serif;
    color: var(--ink);
  }
  .sheet {
    position: relative;
    width: 1200px;
    height: 900px;
    display: flex;
    justify-content: center;
    align-items: center;
    gap: 80px;
  }
  .card {
    position: relative;
    width: 340px;
    height: 595px;
    background: var(--card);
    box-shadow: 0 10px 30px rgba(0,0,0,0.12);
  }

  /* Front: contact side */
  .brand-corner {
    position: absolute;
    top: 38px;
    right: 32px;
    display: flex;
    flex-direction: column;
    align-items: center;
    gap: 8px;
  }
  .brand-corner .ring {
    width: 56px;
    height: 56px;
    border: 2px solid var(--ring);
    border-radius: 50%;
  }
  .brand-corner .brand-name {
    font-size: 13px;
    letter-spacing: 0.08em;
    text-transform: uppercase;
    color: var(--ink);
  }
  .contact-block {
    position: absolute;
    left: 36px;
    bottom: 70px;
    right: 30px;
  }
  .person-name {
    font-size: 27px;
    font-weight: 500;
    letter-spacing: 0.06em;
    text-transform: uppercase;
    line-height: 1;
  }
  .person-role {
    font-size: 14px;
    color: var(--ink-soft);
    margin-top: 8px;
  }
  .divider-bar {
    width: 30px;
    height: 9px;
    background: var(--accent-bar);
    margin: 16px 0 10px;
  }
  .contact-line {
    font-size: 15px;
    line-height: 1.35;
    color: var(--ink);
  }
  .contact-line + .contact-line { margin-top: 10px; }

  /* Back: brand side */
  .card-back {
    display: flex;
    flex-direction: column;
    align-items: center;
    justify-content: center;
    gap: 26px;
  }
  .card-back .ring {
    width: 120px;
    height: 120px;
    border: 3px solid var(--ring);
    border-radius: 50%;
  }
  .card-back .brand-name {
    font-size: 26px;
    letter-spacing: 0.08em;
    text-transform: uppercase;
    color: var(--ink);
  }
</style>
</head>
<body>
  <main class="sheet">
    <section class="card card-front" aria-label="Business card, contact side">
      <div class="brand-corner">
        <div class="ring" aria-hidden="true"></div>
        <span class="brand-name">Corvane Capital</span>
      </div>
      <div class="contact-block">
        <h1 class="person-name">Elias Marrow</h1>
        <p class="person-role">Manager</p>
        <div class="divider-bar" aria-hidden="true"></div>
        <p class="contact-line">4180 Birch Hollow Rd Anchorage,<br>Alaska. 99507, USA</p>
        <div class="divider-bar" aria-hidden="true"></div>
        <p class="contact-line">P:+1 555 014 229</p>
        <p class="contact-line">M:info@corvanecapital.com</p>
        <p class="contact-line">W:www.corvanecapital.com</p>
      </div>
    </section>

    <section class="card card-back" aria-label="Business card, brand side">
      <div class="ring" aria-hidden="true"></div>
      <span class="brand-name">Corvane Capital</span>
    </section>
  </main>
</body>
</html>
```